Business Card Design needed for start up company Halvora

In need of a new business card designed for a start up company based in Sydney, Halvora is a new start up innovative Company, our mission it to make property accessible for everyday Australian and to become the leading Real Estate platform in Australia. We want it to be fresh and clean.

Industry/Entity Type

Financial

Contact Information for Business Card

Section for Name
Section for Title

HALVORA - The Strength of Pooling
Mobile:
Direct:

Font styles to use
Sans Serif

Colors
33a6d7
0692cd
0255a3
ffffff

Requirements
Must have
• Logo, all business card details

```html
<!DOCTYPE html>
<html lang="en">
<head>
<meta charset="utf-8">
<title>Halvora – Business Card</title>
<link rel="stylesheet" href="https://fonts.googleapis.com/css2?family=Open+Sans:wght@400;600;700&display=swap">
<style>
  :root {
    --backdrop: #2a2a2c;
    --card: #262628;
    --card-edge: #303033;
    --sky: #33a6d7;
    --ocean: #0692cd;
    --navy: #0255a3;
    --white: #ffffff;
    --silver: #a9a9ad;
    --soft-text: #e6e6e8;
  }
  * { box-sizing: border-box; margin: 0; padding: 0; }
  html, body {
    width: 1200px; height: 1000px; overflow: hidden;
    background: var(--backdrop);
    font-family: "Open Sans", Arial, sans-serif;
  }
  .stage { position: relative; width: 1200px; height: 1000px; }

  .card {
    position: absolute;
    width: 700px; height: 400px;
    background: var(--card);
    border: 1px solid var(--card-edge);
    box-shadow: 0 18px 40px rgba(0,0,0,.45);
  }
  .card--front { left: 330px; top: 70px; }
  .card--back  { left: 170px; top: 520px; }

  /* Front face: name only, set in the card text font */
  .front-name {
    position: absolute; left: 0; right: 0; top: 50%;
    transform: translateY(-50%);
    text-align: center;
    font-weight: 600; font-size: 54px; letter-spacing: 6px;
    color: var(--silver);
  }

  /* Back face */
  .holder { position: absolute; left: 48px; top: 46px; }
  .holder-name {
    font-weight: 700; font-size: 28px; letter-spacing: 2px;
    color: var(--sky); text-transform: uppercase;
  }
  .holder-title { font-weight: 600; font-size: 17px; color: var(--white); margin-top: 2px; }

  .back-name {
    position: absolute; right: 56px; top: 140px;
    font-weight: 600; font-size: 40px; letter-spacing: 4px;
    color: var(--white);
  }

  .contact-list {
    position: absolute; left: 48px; bottom: 46px;
    list-style: none; display: grid; gap: 6px;
  }
  .contact-list li {
    display: flex; align-items: center; gap: 14px;
    font-size: 19px; color: var(--soft-text); letter-spacing: .5px;
  }
  .contact-list svg { width: 20px; height: 20px; flex: none; }
  .accent { color: var(--sky); }

  .address {
    position: absolute; right: 56px; bottom: 46px;
    text-align: right; font-size: 19px; line-height: 1.3;
    font-style: normal;
    color: var(--soft-text); letter-spacing: .8px;
  }
  .address svg { position: absolute; right: -2px; top: -26px; width: 18px; height: 18px; }
</style>
</head>
<body>
<main class="stage">

  <section class="card card--front" aria-label="Card front">
    <p class="front-name">HALVORA</p>
  </section>

  <section class="card card--back" aria-label="Card back">
    <div class="holder">
      <p class="holder-name">Marcus Reed</p>
      <p class="holder-title">Director</p>
    </div>

    <p class="back-name">HALVORA</p>

    <ul class="contact-list">
      <li>
        <svg viewBox="0 0 20 20"><circle cx="10" cy="10" r="10" fill="var(--sky)"/><path d="M6.5 5.5l2 .2.8 2.2-1.2 1a6 6 0 0 0 3 3l1-1.2 2.2.8.2 2c-4.5.6-8.6-3.5-8-8z" fill="#fff"/></svg>
        <span>000 123 456 789</span>
      </li>
      <li>
        <svg viewBox="0 0 20 20"><circle cx="10" cy="10" r="10" fill="var(--sky)"/><rect x="7" y="4.5" width="6" height="11" rx="1" fill="none" stroke="#fff" stroke-width="1.3"/><circle cx="10" cy="13.5" r=".7" fill="#fff"/></svg>
        <span>000 222 3334</span>
      </li>
      <li>
        <svg viewBox="0 0 20 20"><circle cx="10" cy="10" r="10" fill="var(--sky)"/><rect x="5" y="6.5" width="10" height="7" fill="#fff"/><path d="M5 6.5l5 4 5-4" fill="none" stroke="var(--sky)" stroke-width="1"/></svg>
        <span>urname@email.com</span>
      </li>
      <li>
        <svg viewBox="0 0 20 20"><circle cx="10" cy="10" r="10" fill="var(--sky)"/><g fill="none" stroke="#fff" stroke-width="1.1"><circle cx="10" cy="10" r="5.5"/><ellipse cx="10" cy="10" rx="2.3" ry="5.5"/><path d="M4.5 10h11M5.5 7h9M5.5 13h9"/></g></svg>
        <span>www.<span class="accent">websitename</span>.com</span>
      </li>
    </ul>

    <address class="address">
      <svg viewBox="0 0 20 20"><path d="M3 16L10 3l7 13-7-4z" fill="none" stroke="var(--sky)" stroke-width="1.5"/></svg>
      Your Street Address,<br>Singapore, 1234
    </address>
  </section>

</main>
</body>
</html>
```